Book Cover for Lantern Cousins Notes from the Orchard

We have written a book that brings together Notes from the Orchard from a variety of women's voices.
We developed a draft book cover that we like using Canva (attached below). We'd love a book cover that is similar to this image, but looks more professional.
Following are the themes we’d like to depict in the book cover, and in parentheses, how they are represented in the current cover:
1. Divinely feminine (overall cover)
2. Currents of enlightenment (the swirls of light carrying the butterfly)
3. Diversity (a myriad of colors)
4. The solo journey into the unknown (the single butterfly’s flight)
5. Buoyancy and joy (again, the dancing colors and floating butterfly)
6. Boldly feminine (the blue butterfly, set against brush strokes of light)
7. Homage to a dear friend (she loved blue butterflies, the cosmos - this butterfly has hints of the cosmos in her wings, and painting - this background has brush strokes of light).
Book Title, Subtitle, and Editor:
Lantern Cousins
Notes from the Orchard
Edited by Ilse Varno
Thank you very much for considering this project!
People who are interested in Women and Spirituality

```html
<!DOCTYPE html>
<html lang="en">
<head>
<meta charset="utf-8">
<title>Lantern Cousins — Notes from the Orchard</title>
<link rel="stylesheet" href="https://fonts.googleapis.com/css2?family=Bodoni+Moda:wght@400;500&family=Cinzel:wght@400&display=swap">
<style>
  :root {
    --page-bg: #ffffff;
    --cover-edge: #e62d64;
    --cover-mid: #c52454;
    --cover-glow: #ea5183;
    --title-ink: #f4f0f1;
    --gold: #ecd882;
    --editor-ink: #f6e9ee;
    --wing-deep: #0f4f9e;
    --wing-light: #2fa5e0;
  }
  * { margin: 0; padding: 0; box-sizing: border-box; }
  html, body {
    width: 1200px;
    height: 800px;
    overflow: hidden;
    background: var(--page-bg);
  }
  .book-cover {
    position: absolute;
    left: 353px;
    top: 30px;
    width: 494px;
    height: 740px;
    background:
      radial-gradient(ellipse 60% 25% at 15% 0%, var(--cover-glow) 0%, transparent 70%),
      linear-gradient(90deg, var(--cover-edge) 0%, var(--cover-mid) 45%, var(--cover-mid) 60%, var(--cover-edge) 100%);
    color: var(--title-ink);
    text-align: center;
    overflow: hidden;
  }
  .title-line {
    position: absolute;
    left: 0;
    width: 100%;
    font-family: "Bodoni Moda", serif;
    font-weight: 400;
    font-size: 84px;
    line-height: 1;
    letter-spacing: -3px;
    color: var(--title-ink);
  }
  .title-line--first { top: 62px; }
  .title-line--second { top: 146px; }
  .butterfly-art {
    position: absolute;
    left: 179px;
    top: 287px;
    width: 134px;
    height: 119px;
  }
  .subtitle-flourish {
    position: absolute;
    left: 88px;
    top: 398px;
    width: 310px;
    height: 196px;
  }
  .subtitle-line {
    position: absolute;
    left: 0;
    width: 100%;
    font-family: "Cinzel", serif;
    font-weight: 400;
    font-size: 52px;
    line-height: 1;
    letter-spacing: 4px;
    color: var(--gold);
  }
  .subtitle-line--first { top: 422px; }
  .subtitle-line--second { top: 476px; font-size: 46px; }
  .subtitle-line--third { top: 530px; }
  .editor-credit {
    position: absolute;
    left: 0;
    top: 674px;
    width: 100%;
    font-family: "Bodoni Moda", serif;
    font-weight: 400;
    font-size: 21px;
    letter-spacing: 1px;
    color: var(--editor-ink);
  }
</style>
</head>
<body>
  <main class="book-cover">
    <h1 class="cover-title">
      <span class="title-line title-line--first">LANTERN</span>
      <span class="title-line title-line--second">COUSINS</span>
    </h1>

    <svg class="butterfly-art" viewBox="0 0 134 119" role="img" aria-label="Blue butterfly with starry cosmic wings, resting on the subtitle">
      <defs>
        <radialGradient id="wingTone" cx="45%" cy="45%" r="65%">
          <stop offset="0%" stop-color="var(--wing-light)"/>
          <stop offset="100%" stop-color="var(--wing-deep)"/>
        </radialGradient>
      </defs>
      <rect x="0" y="0" width="134" height="119" rx="40" fill="url(#wingTone)" opacity="0.9"/>
    </svg>

    <svg class="subtitle-flourish" viewBox="0 0 310 196" role="img" aria-label="Fine gold swirling flourish around the subtitle">
      <defs>
        <radialGradient id="flourishTone" cx="50%" cy="50%" r="50%">
          <stop offset="0%" stop-color="var(--gold)" stop-opacity="0.14"/>
          <stop offset="100%" stop-color="var(--gold)" stop-opacity="0"/>
        </radialGradient>
      </defs>
      <rect x="0" y="0" width="310" height="196" fill="url(#flourishTone)"/>
    </svg>

    <h2 class="cover-subtitle">
      <span class="subtitle-line subtitle-line--first">NOTES</span>
      <span class="subtitle-line subtitle-line--second">FROM THE</span>
      <span class="subtitle-line subtitle-line--third">ORCHARD</span>
    </h2>

    <p class="editor-credit">EDITED BY ILSE VARNO</p>
  </main>
</body>
</html>
```